Business Card Design

I already have a company logo for my company. I have a logo for the manufacturer we represent. I want a professional business card design.

```html
<!DOCTYPE html>
<html lang="en">
<head>
<meta charset="utf-8">
<title>Beacon Safeguard LLC – Business Card</title>
<link rel="stylesheet" href="https://fonts.googleapis.com/css2?family=Open+Sans:wght@400;600;700&display=swap">
<style>
  :root {
    --backdrop: #474747;
    --card: #161616;
    --red: #e3232a;
    --white: #f2f2f2;
    --gold: #d4a22a;
  }
  * { margin: 0; padding: 0; box-sizing: border-box; }
  html, body {
    width: 1200px; height: 801px; overflow: hidden;
    background: var(--backdrop);
    font-family: "Open Sans", Arial, sans-serif;
  }
  .card {
    position: absolute;
    width: 530px; height: 303px;
    top: 249px;
    background: var(--card);
    border: 2px solid var(--red);
    border-radius: 16px;
    overflow: hidden;
  }
  .card--front { left: 55px; }
  .card--back { left: 615px; }

  .name-tab {
    position: absolute; right: 0; top: 26px;
    width: 14px; height: 30px;
    background: var(--red);
  }
  .person {
    position: absolute; right: 30px; top: 26px;
    text-align: right;
  }
  .person__name {
    color: var(--red); font-weight: 600;
    font-size: 22px; letter-spacing: 0.5px; line-height: 1.1;
  }
  .person__title {
    color: var(--white); font-size: 14px; margin-top: 2px;
  }

  .brand {
    position: absolute;
    display: flex; align-items: center; gap: 10px;
  }
  .brand__mark { background: var(--red); flex: none; }
  .brand__name {
    color: var(--white); font-weight: 700;
    text-transform: uppercase; line-height: 1.05;
  }
  .card--front .brand { left: 30px; top: 92px; }
  .card--front .brand__mark { width: 22px; height: 22px; }
  .card--front .brand__name { font-size: 19px; }

  .card--back .brand {
    left: 50%; top: 50%; transform: translate(-50%, -50%);
    gap: 16px;
  }
  .card--back .brand__mark { width: 40px; height: 40px; }
  .card--back .brand__name { font-size: 36px; }

  .contact {
    position: absolute; left: 80px; bottom: 26px;
    color: var(--white); font-size: 14px; line-height: 1.35;
  }
  .contact__address { margin-bottom: 10px; }
  .contact__row { display: flex; align-items: center; gap: 8px; }
  .contact__icon { width: 12px; height: 12px; flex: none; }
</style>
</head>
<body>

<section class="card card--front" aria-label="Business card front">
  <span class="name-tab"></span>
  <div class="person">
    <p class="person__name">DANIEL REYES</p>
    <p class="person__title">Managing Director</p>
  </div>

  <div class="brand">
    <span class="brand__mark"></span>
    <p class="brand__name">Beacon Safeguard<br>LLC</p>
  </div>

  <div class="contact">
    <p class="contact__address">Your address, City<br>State, Zip 1234</p>
    <p class="contact__row">
      <svg class="contact__icon" viewBox="0 0 24 24"><path fill="#e3232a" d="M6.6 10.8a15 15 0 0 0 6.6 6.6l2.2-2.2a1 1 0 0 1 1-.25 11.4 11.4 0 0 0 3.6.57 1 1 0 0 1 1 1V20a1 1 0 0 1-1 1A17 17 0 0 1 3 4a1 1 0 0 1 1-1h3.5a1 1 0 0 1 1 1c0 1.25.2 2.45.57 3.57a1 1 0 0 1-.25 1z"/></svg>
      123 456 789
    </p>
    <p class="contact__row">
      <svg class="contact__icon" viewBox="0 0 24 24"><rect x="2" y="5" width="20" height="14" rx="2" fill="#e3232a"/><path d="M3 6l9 7 9-7" stroke="#161616" stroke-width="2" fill="none"/></svg>
      info@yourmail.com
    </p>
    <p class="contact__row">
      <svg class="contact__icon" viewBox="0 0 24 24"><circle cx="12" cy="12" r="10" fill="#e3232a"/><path d="M2 12h20M12 2c3 3 3 17 0 20M12 2c-3 3-3 17 0 20" stroke="#161616" stroke-width="1.5" fill="none"/></svg>
      www.yourwebsite.com
    </p>
  </div>
</section>

<section class="card card--back" aria-label="Business card back">
  <div class="brand">
    <span class="brand__mark"></span>
    <p class="brand__name">Beacon Safeguard<br>LLC</p>
  </div>
</section>

</body>
</html>
```